Executive recruiting firm in need of business card design

Executive recruiting firm looking for a sleek, classy and modern business card design; card itself will be square shape, rounded edges and soft touch paper, our colors are dark blues in the navy color scale, silvers and grays. Reference our website for a better idea of our company's feel and goals at Tarvex-Up.com - our company message is "Employee Engagement Begins at Recruitment" this should be on the card

```html
<!DOCTYPE html>
<html lang="en">
<head>
<meta charset="utf-8">
<title>Tarvex-Up Business Card</title>
<link rel="stylesheet" href="https://fonts.googleapis.com/css2?family=Roboto:wght@400&family=Roboto+Condensed:wght@400;600&display=swap">
<style>
  :root {
    --navy: #141540;
    --paper: #f4f4f3;
    --backdrop: #a8a8a8;
    --ink: #4a4a4a;
    --white: #ffffff;
  }
  * { margin: 0; padding: 0; box-sizing: border-box; }
  html, body { width: 1200px; height: 960px; overflow: hidden; }
  body {
    background: var(--backdrop);
    position: relative;
    font-family: "Roboto", Arial, sans-serif;
  }
  .card {
    position: absolute;
    background: var(--paper);
  }
  .card--front { left: 320px; top: 100px; width: 602px; height: 350px; }
  .card--back  { left: 320px; top: 493px; width: 600px; height: 342px; }

  .company-name {
    position: absolute;
    font-family: "Roboto", Arial, sans-serif;
    font-weight: 400;
    color: var(--navy);
    line-height: 1;
    white-space: nowrap;
  }
  .card--front .company-name {
    left: 0; right: 0; top: 142px;
    text-align: center;
    font-size: 44px;
  }
  .card--back .company-name {
    left: 46px; top: 243px;
    font-size: 28px;
  }

  .motto {
    position: absolute;
    left: 0; right: 0; top: 290px;
    text-align: center;
    font-size: 14px;
    color: var(--ink);
  }

  .name-band {
    position: absolute;
    left: 316px; top: 50px;
    width: 284px; height: 75px;
    background: var(--navy);
    border-radius: 38px 0 0 38px;
    padding: 15px 0 0 48px;
    color: var(--white);
    font-family: "Roboto Condensed", Arial, sans-serif;
  }
  .name-band__name { font-size: 21px; font-weight: 600; line-height: 1.2; }
  .name-band__role { font-size: 14px; font-weight: 400; margin-top: 2px; letter-spacing: 0.3px; }

  .contacts {
    position: absolute;
    left: 364px; top: 164px;
    list-style: none;
    font-size: 14px;
    color: var(--ink);
  }
  .contacts li { display: flex; align-items: flex-start; line-height: 19px; }
  .contacts li.contacts__address { margin-bottom: 9px; }
  .contacts svg { width: 13px; height: 13px; margin: 3px 19px 0 0; flex: none; fill: var(--navy); }
</style>
</head>
<body>

<section class="card card--front" aria-label="Card front">
  <span class="company-name">Tarvex Up</span>
  <p class="motto">Employee Engagement Begins at Recruitment</p>
</section>

<section class="card card--back" aria-label="Card back">
  <div class="name-band">
    <div class="name-band__name">DANIEL MARSH</div>
    <div class="name-band__role">CEO/FOUNDER</div>
  </div>

  <ul class="contacts">
    <li class="contacts__address">
      <svg viewBox="0 0 16 16"><path d="M8 0a5.5 5.5 0 0 0-5.5 5.5C2.5 10 8 16 8 16s5.5-6 5.5-10.5A5.5 5.5 0 0 0 8 0zm0 8a2.5 2.5 0 1 1 0-5 2.5 2.5 0 0 1 0 5z"/></svg>
      <span>240 West Alder Ave.<br>Fairview, CA</span>
    </li>
    <li>
      <svg viewBox="0 0 16 16"><path d="M3.6 0.8l2.3 2.9c.3.4.3 1-.1 1.4L4.6 6.3c.9 2 2.9 4 5.1 5.1l1.2-1.2c.4-.4 1-.4 1.4-.1l2.9 2.3c.4.3.5 1 .1 1.4l-1.4 1.4C10.5 16.6 -0.6 5.5 0.8 2.1L2.2.7c.4-.4 1.1-.3 1.4.1z"/></svg>
      <span>555 214 7730</span>
    </li>
    <li>
      <svg viewBox="0 0 16 16"><path d="M4.5 0h7A1.5 1.5 0 0 1 13 1.5v13a1.5 1.5 0 0 1-1.5 1.5h-7A1.5 1.5 0 0 1 3 14.5v-13A1.5 1.5 0 0 1 4.5 0zM5 2v10h6V2zm3 11a1 1 0 1 0 0 2 1 1 0 0 0 0-2z"/></svg>
      <span>555 902 6418</span>
    </li>
    <li>
      <svg viewBox="0 0 16 16"><path d="M4 0h6l2 2v3H4zM1.5 6h13A1.5 1.5 0 0 1 16 7.5V13h-3v3H3v-3H0V7.5A1.5 1.5 0 0 1 1.5 6zM5 11v3h6v-3z"/></svg>
      <span>555 377 0152</span>
    </li>
    <li>
      <svg viewBox="0 0 16 16"><path d="M0 3h16v1.2L8 9 0 4.2zM0 5.8l8 4.8 8-4.8V13H0z"/></svg>
      <span>daniel@tarvex-up.com</span>
    </li>
    <li>
      <svg viewBox="0 0 16 16"><path d="M8 0a8 8 0 1 0 0 16A8 8 0 0 0 8 0zm3.5 4.5c.6 1.3-.6 1.8-1.5 1.5-1-.4-1.8.6-1 1.6.7 1 2 .8 2.2 2.2.1 1-.8 2-1.4 3-.5-1.5-1.8-2-1.9-3.3-.1-1-1.4-1-2.3-1.8C4.7 6.9 5.3 5 4 4.2 5.2 2.6 6.9 2 8.6 2.1c-.5.8.2 1.7 1 1.4.7-.2 1.4.3 1.900 1z"/></svg>
      <span>www.tarvex-up.com</span>
    </li>
  </ul>

  <span class="company-name">Tarvex Up</span>
</section>

</body>
</html>
```